Global Beard Oil Review Business needs a refresh

topwhiskertonic.net is a global business who's mission is to curate all available beard oils from around the world, review and grade them and present this curated collection to the user of the website.

The scope of this job includes the web site design and the design of a suitable logo to be used in the site header.

The existing site can be seen on http://topwhiskertonic.net, however this is a mock-up only the style and logo should NOT be used. This is to give you an idea of the concept of the site only.

This job is for PSD design only.

See attached design brief for detailed design requirements.
Updates

Project Deadline Extended
Reason: Extending deadline by 5 days to allow for final submissions

Target Market(s)

Men's grooming / retail

Industry/Entity Type

Retail

Number of Pages Required

2 page

Font styles to use
Sans Serif

Requirements
Must have
• 1) Comparison Table
• 2) Side Bar
• 3) Header area
• 4) Photo of Delvin Marsk (attached - can be circular or "cut-out")
• 5) Cool beard-oriented custom design background (e.g., stylistic black/brown on brown/orange beard background. I envision this beard background "drawing" rather than photo based)
• (see attached design requirements for details)
Nice to have
• Signature style writing at top with name "Delvin Marsk"
Should not have
• Do NOT use the look & feel or logo from the existing site.

```html
<!DOCTYPE html>
<html lang="en">
<head>
<meta charset="utf-8">
<title>Top Whisker Tonic</title>
<link href="https://fonts.googleapis.com/css2?family=Raleway:wght@400;600&family=Roboto+Condensed:wght@400&family=Lato:wght@400;700&family=Alex+Brush&display=swap" rel="stylesheet">
<style>
:root{--teal:#3cb3ad;--orange:#f7962e;--dark:#2a2e36;--ink:#333;--row-a:#e3e3e3;--row-b:#efefef;--line:#bbb}
*{box-sizing:border-box;margin:0;padding:0}
html,body{width:886px;height:1200px;overflow:hidden}
body{position:relative;background:#fafafa;font-family:'Lato',sans-serif;color:var(--ink)}
.abs{position:absolute}
.site-header{left:0;top:0;width:886px;height:78px;background:var(--dark)}
.brand{left:146px;top:26px;font-family:'Raleway',sans-serif;font-weight:600;font-size:19px;color:var(--teal);white-space:nowrap}
.nav{top:30px;font-family:'Roboto Condensed',sans-serif;font-size:11px;color:#fff;line-height:22px}
.nav-home{left:366px;width:49px;height:22px;border:1.5px solid var(--teal);border-radius:3px;text-align:center;color:var(--teal)}
.hero{left:0;top:78px;width:886px;height:306px;background:linear-gradient(180deg,#ebe8e4 0%,#e6e1db 55%,#d6cfc4 100%)}
.hero-photo{left:500px;top:0;width:386px;height:306px;background:radial-gradient(ellipse at 78% 60%,#5a3418 0 18%,rgba(120,80,50,.35) 30%,rgba(230,225,219,0) 60%)}
.hero-title{left:146px;top:164px;font-family:'Raleway',sans-serif;font-size:28px;line-height:28px;color:#333}
.hero-title b{font-weight:600}
.o{color:var(--orange)}.t{color:var(--teal)}
.btn{border:1.5px solid var(--teal);border-radius:3px;color:var(--teal);font-family:'Roboto Condensed',sans-serif;font-size:11px;text-align:center;line-height:19px;background:#fff}
.btn-dark{left:147px;top:269px;width:67px;height:22px;border-color:#333;color:#333;background:transparent}
.dot{top:357px;width:9px;height:9px;border-radius:50%;background:#fff}
.h2{font-family:'Raleway',sans-serif;font-size:23px;color:var(--teal);white-space:nowrap}
.rule{height:1px;background:var(--line)}
.rule:before{content:"";display:block;width:36px;height:2px;background:#666;margin-top:-1px}
.copy{font-size:8.6px;line-height:11.6px;color:#444}
table{border-collapse:collapse;font-size:8.6px}
th{background:var(--teal);color:#fff;font-family:'Roboto Condensed',sans-serif;font-weight:400;font-size:9.5px;height:29px;border-right:1px solid #fff;line-height:10px}
td{height:61px;vertical-align:top;border-right:1px solid #fff;padding-top:8px}
tr:nth-child(odd) td{background:var(--row-a)}
tr:nth-child(even) td{background:var(--row-b)}
.sn div{padding-left:5px;line-height:16px}.sn b{color:var(--orange);font-weight:700}
.thumb{display:block;margin:2px auto 0;width:36px;height:44px;background:linear-gradient(#7a6a5a,#2a221c);border:2px solid #f3ead9}
.obs div{padding-left:8px;line-height:15.5px}
.scores div{font-family:'Roboto Condensed',sans-serif;font-size:10px;line-height:15.5px;display:flex}
.scores span{width:46px;text-align:right;margin-right:11px}
.buy{display:block;margin:19px auto 0;width:43px;height:16px;background:var(--orange);color:#fff;border-radius:3px;font-size:7.5px;line-height:16px;text-align:center;box-shadow:0 1px 1px #a55}
.sidebar{left:554px;top:402px;width:185px;height:655px;background:#fff;box-shadow:0 0 4px rgba(0,0,0,.15)}
.portrait{left:564px;top:413px;width:164px;height:178px;border:1px solid #ccc;padding:4px}
.portrait div{width:100%;height:100%;background:linear-gradient(160deg,#cfcfcf,#6c6c6c 60%,#3a3a3a)}
.signature{left:554px;top:596px;width:185px;text-align:center;font-family:'Alex Brush',cursive;font-size:22px;color:#222}
.date{left:565px;width:30px;height:29px;background:var(--orange);color:#fff;font-size:9px;font-weight:700;line-height:12px;padding:3px 0 0 5px}
.date sup{font-size:6px}
.post-title{left:604px;font-size:8.6px;font-weight:700;line-height:12px;width:125px}
.post-img{left:565px;width:162px;height:55px;border:1px solid #ccc}
.sep{left:565px;width:162px;height:1px;background:#ddd}
.more{color:var(--orange)}
.footer-band{left:0;top:1090px;width:886px;height:38px;background:var(--orange);text-align:center;color:#fff;font-size:8.6px;line-height:38px}
.site-footer{left:0;top:1128px;width:886px;height:72px;background:var(--dark)}
.ficon{top:1145px;width:23px;height:23px;border-radius:50%}
.social{top:1151px;width:18px;height:18px;border-radius:50%;background:#fff}
</style>
</head>
<body>
<header class="abs site-header"></header>
<div class="abs brand">TOP WHISKER TONIC</div>
<div class="abs nav nav-home">Home</div>
<div class="abs nav" style="left:432px">About Me</div>
<div class="abs nav" style="left:504px">Our Charter</div>
<div class="abs nav" style="left:584px">Beard Oil Methodology</div>
<div class="abs nav" style="left:713px">BLog</div>

<section class="abs hero">
  <div class="abs hero-photo" role="img" aria-label="Photo of three amber dropper bottles of beard oil on a wooden table"></div>
</section>
<h1 class="abs hero-title" style="font-weight:400"><b class="o">Beard Oil</b> with <b class="t">Argan Kukui</b><br><b class="t">Babbasu Citrus</b> Mint<br>Essential Oils</h1>
<div class="abs btn btn-dark">Read More</div>
<span class="abs dot" style="left:426px;background:var(--dark)"></span>
<span class="abs dot" style="left:442px"></span>
<span class="abs dot" style="left:459px"></span>

<h2 class="abs h2" style="left:148px;top:408px">About <span class="o">Delvin Marsk</span></h2>
<div class="abs rule" style="left:148px;top:438px;width:393px"></div>
<p class="abs copy" style="left:148px;top:449px;width:394px">Sed ut perspiciatis unde omnis iste natus error sit voluptatem accusantium doloremque laudantium, totam rem aperiam, eaque ipsa quae ab illo inventore veritatis et quasi architecto beatae vitae dicta sunt explicabo. Nemo enim ipsam voluptatem quia voluptas sit aspernatur aut odit aut fugit, sed quia consequuntur magni dolores eos qui ratione voluptatem sequi nesciunt. Neque porro quisquam est, qui dolorem ipsum quia dolor sit amet, consectetur, adipisci velit, sed quia non numquam eius modi tempora incidunt ut labore et dolore magnam aliquam quaerat voluptatem.</p>
<p class="abs copy" style="left:148px;top:538px;width:394px">Sed ut perspiciatis unde omnis iste natus error sit voluptatem accusantium doloremque laudantium, totam rem aperiam, eaque ipsa quae ab illo inventore veritatis et quasi architecto beatae vitae dicta sunt explicabo.</p>
<div class="abs btn" style="left:147px;top:586px;width:71px;height:22px">Read More</div>

<h2 class="abs h2" style="left:148px;top:648px">The World's #1 <span class="o">Beard Oil Authority</span></h2>
<div class="abs rule" style="left:148px;top:684px;width:393px"></div>
<p class="abs copy" style="left:148px;top:693px;width:394px;line-height:12.6px">Here is the master list of beard oils reviewed to date. You can link directly to the corresponding review by clicking on the name of the beard oil. In accordance with our charter, we are actively working to locate and review every single beard oil available on the planet Earth.</p>

<table class="abs" style="left:147px;top:743px;width:395px">
  <thead><tr><th style="width:99px">Supplier &amp; Name</th><th style="width:49px">Photo</th><th style="width:111px">Origin,Base Oil,Scent</th><th style="width:74px">Affect,Value,<br>Overall</th><th style="width:62px;border-right:0">Links</th></tr></thead>
  <tbody>
    <tr><td class="sn"><div><b>S:</b> Grizzled Gent</div><div><b>N:</b> Timberline</div></td><td><span class="thumb" role="img" aria-label="Beard oil bottle"></span></td><td class="obs"><div>O: Spiciatis</div><div>B: Modi Tempora</div><div>S: Quia</div></td><td class="scores"><div><span>Affect:</span>7</div><div><span>Value:</span>5</div><div><span>Overall:</span>5</div></td><td style="border-right:0"><span class="buy">Buy Now</span></td></tr>
    <tr><td class="sn"><div><b>S:</b> Grizzled Gent</div><div><b>N:</b> Timberline</div></td><td><span class="thumb" role="img" aria-label="Beard oil bottle"></span></td><td class="obs"><div>O: Spiciatis</div><div>B: Modi Tempora</div><div>S: Quia</div></td><td class="scores"><div><span>Affect:</span>7</div><div><span>Value:</span>5</div><div><span>Overall:</span>5</div></td><td style="border-right:0"><span class="buy">Buy Now</span></td></tr>
    <tr><td class="sn"><div><b>S:</b> Grizzled Gent</div><div><b>N:</b> Timberline</div></td><td><span class="thumb" role="img" aria-label="Beard oil bottle"></span></td><td class="obs"><div>O: Spiciatis</div><div>B: Modi Tempora</div><div>S: Quia</div></td><td class="scores"><div><span>Affect:</span>7</div><div><span>Value:</span>5</div><div><span>Overall:</span>5</div></td><td style="border-right:0"><span class="buy">Buy Now</span></td></tr>
    <tr><td class="sn"><div><b>S:</b> Grizzled Gent</div><div><b>N:</b> Timberline</div></td><td><span class="thumb" role="img" aria-label="Beard oil bottle"></span></td><td class="obs"><div>O: Spiciatis</div><div>B: Modi Tempora</div><div>S: Quia</div></td><td class="scores"><div><span>Affect:</span>7</div><div><span>Value:</span>5</div><div><span>Overall:</span>5</div></td><td style="border-right:0"><span class="buy">Buy Now</span></td></tr>
  </tbody>
</table>
<div class="abs btn" style="left:147px;top:1034px;width:71px;height:22px">Load More</div>
<svg class="abs" style="left:228px;top:1035px" width="20" height="20" viewBox="0 0 20 20"><path d="M5 6 A7 7 0 1 1 4 13" fill="none" stroke="#111" stroke-width="2.2"/><path d="M1 5 L7 3 L6 9 Z" fill="#111"/></svg>

<aside class="abs sidebar"></aside>
<div class="abs portrait"><div role="img" aria-label="Black and white portrait photo of Delvin Marsk"></div></div>
<div class="abs signature">Delvin Marsk</div>
<h2 class="abs h2" style="left:566px;top:654px">Latest <span class="o">Blog</span></h2>
<div class="abs rule" style="left:566px;top:684px;width:161px"></div>

<div class="abs date" style="top:700px">12<sup>th</sup><br>Feb</div>
<div class="abs post-title" style="top:701px">Lorem ipsum dolor sit amet, consectetuer</div>
<div class="abs post-img" style="top:734px;background:linear-gradient(90deg,#3d4a2a,#8a9a5a 50%,#2e3a22)" role="img" aria-label="Close-up photo of a dropper releasing oil"></div>
<p class="abs copy" style="left:564px;top:796px;width:166px">Sed ut perspiciatis unde omnis iste natus error sit voluptatem accusantium dolor emque laudantium, <span class="more">+</span></p>
<div class="abs sep" style="top:839px"></div>

<div class="abs date" style="top:861px">12<sup>th</sup><br>Feb</div>
<div class="abs post-title" style="top:862px">Lorem ipsum dolor sit amet, consectetuer</div>
<div class="abs post-img" style="top:895px;background:linear-gradient(180deg,#d8cba8,#bfa97a)" role="img" aria-label="Photo of a beard oil bottle on sand"></div>
<p class="abs copy" style="left:564px;top:957px;width:166px">Sed ut perspiciatis unde omnis iste natus error sit voluptatem accusantium dolor emque laudantium, <span class="more">+</span></p>
<div class="abs sep" style="top:1000px"></div>
<div class="abs btn" style="left:565px;top:1011px;width:72px;height:23px">Read All</div>

<nav class="abs footer-band">Home &nbsp;|&nbsp; About Me &nbsp;|&nbsp; Our Charter &nbsp;|&nbsp; Beard Oil Methodology &nbsp;|&nbsp; Blog</nav>
<footer class="abs site-footer"></footer>
<span class="abs ficon" style="left:166px;background:var(--orange)"></span>
<svg class="abs" style="left:174px;top:1150px" width="8" height="13"><rect x="0.7" y="0.7" width="6.6" height="11.6" rx="1" fill="none" stroke="#fff" stroke-width="1.2"/><rect x="3" y="9.5" width="2" height="1.3" fill="#fff"/></svg>
<span class="abs ficon" style="left:189px;background:#444"></span>
<svg class="abs" style="left:194px;top:1152px" width="13" height="9"><rect x="0.6" y="0.6" width="11.8" height="7.8" fill="none" stroke="#fff" stroke-width="1.2"/><path d="M1 1 L6.5 5 L12 1" fill="none" stroke="#fff" stroke-width="1.2"/></svg>
<div class="abs brand" style="left:222px;top:1150px;font-size:15px">TOP WHISKER TONIC</div>
<div class="abs" style="left:582px;top:1151px;font-family:'Raleway',sans-serif;font-weight:600;font-size:13px;color:#fff">Follow Us</div>
<span class="abs social" style="left:655px"></span>
<span class="abs social" style="left:678px"></span>
<span class="abs social" style="left:700px"></span>
<span class="abs social" style="left:722px"></span>
<div class="abs" style="left:167px;top:1179px;font-size:7.5px;color:#ddd">Copyright © 2016 Top Whisker Tonic. All rights reserved.</div>
</body>
</html>
```